"Vine Hollow Excursions" is a top notch Santa Barbara County Wine Tour company.

We provide scenic, boutique and custom wine tours. I need the card to be clean and classy. I will provide our logo. I would like the logo to cover the back side of the card as an option and would like to see a couple color options other then our signature green and gold. I would like to see some creative options and let the designers come up with options.
I need cards for myself and my team. The final design should communicate "Unhurried, personal journeys through local vineyards"
Please use my website for reference www.vinehollowexcursions.example

Target Market(s)

We have a wide range of clients from millennials to baby boomers

Industry/Entity Type

Tour

Contact Information for Business Card

Contact info:
Dale Morton
805-219-6384
info@vinehollowexcursions.example
vinehollowexcursions.example

Colors

Designer to choose colors to be used in the design.

Requirements
Must have
• my logo
Nice to have
• *I would like to have the backside side with the logo and the company statement
• "Unhurried, personal journeys through local vineyards" as an option.
• *I would also like to see what the designers can create!
• *I would like to see an option that incorporates or social: instagram, yelp, trip advisor
Should not have
• I do not want it too busy.

```html
<!DOCTYPE html>
<html lang="en">
<head>
<meta charset="utf-8">
<title>Vine Hollow Excursions – Business Card</title>
<link href="https://fonts.googleapis.com/css2?family=Cinzel:wght@500;700&family=Nunito+Sans:wght@300;400;700&display=swap" rel="stylesheet">
<style>
  :root {
    --bg: #666666;
    --card-white: #ffffff;
    --green: #1f5e3a;
    --green-deep: #0d4529;
    --green-mid: #1b6a42;
    --gold: #b8934d;
    --text-dark: #2b2b2b;
    --rule: #3a3a3a;
  }
  * { margin: 0; padding: 0; box-sizing: border-box; }
  html, body { width: 1200px; height: 1008px; overflow: hidden; }
  body { background: var(--bg); position: relative; font-family: "Nunito Sans", sans-serif; }

  .card { position: absolute; left: 316px; width: 560px; height: 320px; overflow: hidden; }
  .card-front { top: 166px; background: var(--card-white); }
  .card-back { top: 527px; background: var(--green-deep); }

  /* Front */
  .brand { position: absolute; left: 44px; top: 88px; display: flex; align-items: center; gap: 10px; }
  .brand-dot { width: 14px; height: 14px; border-radius: 50%; background: var(--gold); }
  .brand-name { font-family: "Cinzel", serif; font-weight: 500; font-size: 24px; color: var(--green); letter-spacing: 0.5px; white-space: nowrap; }

  .person-name { position: absolute; right: 45px; top: 180px; font-family: "Cinzel", serif; font-weight: 700; font-size: 19px; color: var(--green); letter-spacing: 0.5px; }
  .divider { position: absolute; left: 44px; top: 216px; width: 386px; height: 1px; background: var(--rule); }
  .person-title { position: absolute; right: 45px; top: 205px; font-size: 16px; font-weight: 300; color: var(--text-dark); }

  .social { position: absolute; display: flex; gap: 8px; }
  .social-dot { width: 13px; height: 13px; border-radius: 50%; }
  .social-front { right: 45px; top: 237px; }
  .social-front .social-dot { background: var(--green); }

  .contact-list { position: absolute; left: 44px; top: 235px; list-style: none; }
  .contact-list li { display: flex; align-items: center; gap: 9px; height: 20.5px; font-size: 16px; font-weight: 300; color: var(--text-dark); }
  .contact-list svg { width: 16px; height: 16px; flex: none; }
  .contact-list strong { font-weight: 700; color: var(--green); }

  .address { position: absolute; right: 45px; top: 256px; text-align: right; font-size: 16px; font-weight: 300; color: var(--text-dark); line-height: 20.5px; }

  /* Back */
  .back-scenery { position: absolute; inset: 0; background:
      radial-gradient(ellipse 60% 55% at 18% 40%, rgba(60,140,90,0.35), transparent 70%),
      radial-gradient(ellipse 80% 60% at 55% 35%, var(--green-mid), transparent 75%),
      linear-gradient(180deg, #17603b 0%, var(--green-deep) 100%); }
  .back-content { position: absolute; inset: 0; text-align: center; }
  .back-dot { position: absolute; left: 50%; top: 112px; width: 30px; height: 30px; margin-left: -15px; border-radius: 50%; background: var(--gold); }
  .back-name { position: absolute; left: 0; right: 0; top: 170px; font-family: "Cinzel", serif; font-weight: 500; font-size: 29px; color: #ffffff; letter-spacing: 1px; }
  .social-back { left: 50%; transform: translateX(-50%); top: 257px; }
  .social-back .social-dot { background: var(--gold); }
  .tagline { position: absolute; left: 0; right: 0; top: 282px; font-family: "Cinzel", serif; font-weight: 500; font-size: 13px; color: #ffffff; letter-spacing: 0.4px; }
</style>
</head>
<body>

<section class="card card-front" aria-label="Business card front">
  <div class="brand">
    <span class="brand-dot"></span>
    <span class="brand-name">Vine Hollow Excursions</span>
  </div>

  <div class="person-name">DALE MORTON</div>
  <div class="divider"></div>
  <div class="person-title">Your Title</div>

  <div class="social social-front" aria-label="Social profiles">
    <span class="social-dot"></span><span class="social-dot"></span><span class="social-dot"></span>
  </div>

  <ul class="contact-list">
    <li>
      <svg viewBox="0 0 16 16" aria-hidden="true"><rect x="1" y="3" width="14" height="10" fill="var(--green)"/><path d="M1 3 L8 9 L15 3" fill="none" stroke="#fff" stroke-width="1.3"/></svg>
      info@vinehollowexcursions.example
    </li>
    <li>
      <svg viewBox="0 0 16 16" aria-hidden="true"><path d="M1 5 Q8 0 15 5 L13 7 L11 5.5 L5 5.5 L3 7 Z" fill="var(--green)"/><rect x="3.5" y="7.5" width="9" height="6.5" rx="1" fill="var(--green)"/></svg>
      805-219-6384
    </li>
    <li>
      <svg viewBox="0 0 16 16" aria-hidden="true" fill="none" stroke="var(--green)" stroke-width="1.2"><circle cx="8" cy="8" r="6.5"/><ellipse cx="8" cy="8" rx="3" ry="6.5"/><path d="M1.5 8 H14.5 M2.5 4.8 H13.5 M2.5 11.2 H13.5"/></svg>
      <span><strong>vinehollowexcursions</strong>.example</span>
    </li>
  </ul>

  <div class="address">Your Address Goes Here<br>Address Line 2</div>
</section>

<section class="card card-back" aria-label="Business card back">
  <div class="back-scenery" role="img" aria-label="Faint sunrise over hills and vineyard rows in deep green tones"></div>
  <div class="back-content">
    <span class="back-dot"></span>
    <div class="back-name">VINE HOLLOW EXCURSIONS</div>
    <div class="social social-back" aria-label="Social profiles">
      <span class="social-dot"></span><span class="social-dot"></span><span class="social-dot"></span>
    </div>
    <div class="tagline">Unhurried, Personal Journeys Through Local Vineyards</div>
  </div>
</section>

</body>
</html>
```